Patent Law

Need to develop a home page for a patent lawyer.

Colors should go with logo, blues...

Company Name- Velun Tresk, PLLC

Company Overview-

I am an Intellectual Property Lawyer and focus on patents, copyrights, trademarks, & trade secrets. I work with small businesses and start ups in the chemical and biotech industries.

Why Us-

I am small firm that can provide large-firm service at a reasonable price. I also can charge flat-fees for entreprenuers in certain practice areas.

Services-
Intellectual Property
Patents
Copyrights
Trademarks
Trade secrets
Healthcare Compliance
Elder law
Wills
Trusts

Website we like-
http://www.quorvantlegal.example/ - within industry!!
http://www.daltrowemiko.example/
http://ulbrixtane.example/
http://thegravelcounsel.example/

Target Market(s)

My customers will be small business, specifically small start-up companies in the chemical and biotech arena.

Industry/Entity Type

Trade

Requirements
Must have
• Colors should go with logo, blues...

```html
<!DOCTYPE html>
<html lang="en">
<head>
<meta charset="utf-8">
<title>Velun Tresk, PLLC</title>
<link rel="stylesheet" href="https://fonts.googleapis.com/css2?family=Open+Sans:wght@400;600;700&family=Roboto+Slab:wght@300;400;700&family=Noto+Serif:ital@1&display=swap">
<style>
:root{
  --navy:#1d2470;
  --navy-deep:#050a1f;
  --hero-dark:#030a1c;
  --hero-blue:#1f3d78;
  --sky:#1b8fd6;
  --ink:#3d3d3d;
  --muted:#555;
  --paper:#f3f3f3;
  --line:#d6d6d6;
  --white:#fff;
}
*{box-sizing:border-box;margin:0;padding:0}
html,body{width:1200px;height:1040px;overflow:hidden}
body{background:var(--paper);font-family:"Open Sans",sans-serif;color:var(--ink);position:relative}
.site-header{position:absolute;top:0;left:0;width:1200px;height:78px;background:var(--white);border-bottom:1px solid #e2e2e2}
.brand{position:absolute;left:240px;top:10px;width:104px;display:flex;flex-direction:column;align-items:center;gap:6px}
.brand-dot{width:34px;height:34px;border-radius:50%;background:var(--navy)}
.brand-name{font-family:"Roboto Slab",serif;font-weight:400;font-size:10px;letter-spacing:.3px;color:var(--navy);text-transform:uppercase;white-space:nowrap}
.header-divider{position:absolute;left:356px;top:14px;width:1px;height:56px;background:#e0e0e0}
.main-nav a{position:absolute;top:32px;font-size:10.5px;color:#2b2b2b;text-decoration:none;white-space:nowrap}
.main-nav a.active::after{content:"";position:absolute;left:-10px;right:-9px;top:19px;height:3px;background:var(--navy)}
.contact-top{position:absolute;right:246px;top:23px;text-align:right;font-size:14px;color:#222;line-height:17px}
.contact-top svg{vertical-align:-1px;margin-right:3px}
.hero{position:absolute;top:78px;left:0;width:1200px;height:399px;background:linear-gradient(90deg,var(--hero-dark) 0%,#061331 45%,#0a1c44 70%,var(--hero-dark) 100%);overflow:hidden}
.hero-visual{position:absolute;left:490px;top:0;width:600px;height:399px;background:radial-gradient(ellipse at 58% 40%,#3a5a9a 0%,var(--hero-blue) 35%,#0b1a3f 70%,transparent 100%)}
.hero-copy{position:absolute;left:240px;top:102px;width:420px}
.hero-title{font-family:"Roboto Slab",serif;font-weight:700;font-size:41px;line-height:49px;color:var(--sky);text-transform:uppercase;white-space:nowrap}
.hero-text{margin-top:6px;font-size:12.5px;font-weight:700;line-height:18px;color:var(--white)}
.btn-light{display:inline-block;margin-top:14px;padding:6px 10px;font-size:13px;font-weight:600;color:#333;background:linear-gradient(#fdfdfd,#cfcfcf);border:1px solid #9a9a9a;border-radius:5px}
.arrow{position:absolute;top:185px;width:29px;height:29px;border-radius:50%;background:var(--white)}
.arrow svg{position:absolute;left:9px;top:8px}
.intro{position:absolute;top:488px;left:0;width:1200px;text-align:center}
.intro h1{font-family:"Roboto Slab",serif;font-weight:300;font-size:28px;color:#555}
.intro h1 strong{font-weight:400;color:var(--navy)}
.intro p{width:710px;margin:8px auto 0;font-size:10px;line-height:13.5px;color:#555}
.intro-actions{margin-top:16px;display:flex;justify-content:center;gap:10px}
.btn{width:92px;height:33px;border-radius:4px;font-size:11px;color:var(--white);display:flex;align-items:center;justify-content:center}
.btn-dark{background:linear-gradient(#6a6a6a,#3c3c3c);border:2px solid #a8a8a8}
.btn-navy{background:linear-gradient(#3a3f9a,#1d2470);border:2px solid #5a63c8}
.rule{position:absolute;left:240px;width:714px;height:4px;border-top:1px dotted #cfcfcf;border-bottom:1px dotted #cfcfcf}
.columns{position:absolute;top:652px;left:240px;width:714px;display:flex}
.col h2{font-family:"Roboto Slab",serif;font-weight:400;font-size:15px;color:#444;margin-bottom:6px}
.col p{font-size:9.5px;line-height:13.5px;color:#555}
.col-why{width:243px;padding-right:40px}
.col-what{width:242px}
.col-contact{width:229px}
.services{list-style:none;font-size:9.5px;line-height:13.2px;color:#555}
.services li::before{content:"";display:inline-block;border-left:3px solid var(--navy);border-top:3px solid transparent;border-bottom:3px solid transparent;margin-right:4px;vertical-align:1px}
.office{font-size:11px;font-weight:700;color:var(--navy);margin-top:2px}
.office+p{margin-bottom:2px}
.btn-small{display:inline-block;margin-top:12px;padding:4px 6px;font-size:9px;color:var(--white);background:linear-gradient(#5a5a5a,#333);border-radius:3px}
.subscribe-band{position:absolute;top:857px;left:240px;width:714px;height:73px;background:var(--white);border:1px solid #cfcfcf}
.quote-mark{position:absolute;left:28px;top:14px;font-family:"Roboto Slab",serif;font-size:60px;line-height:60px;color:#9a9a9a}
.quote-text{position:absolute;left:80px;top:21px;width:300px;font-family:"Noto Serif",serif;font-style:italic;font-size:9.5px;line-height:13.5px;color:#555}
.dots{position:absolute;left:357px;top:56px;display:flex;gap:3px}
.dots span{width:7px;height:7px;border-radius:50%;background:#bbb}
.dots span:first-child{background:var(--navy)}
.band-divider{position:absolute;left:398px;top:10px;width:1px;height:52px;background:#e4e4e4}
.email{position:absolute;left:420px;top:22px;width:225px;height:25px;border:1px solid #cfcfcf;font-family:"Noto Serif",serif;font-style:italic;font-size:9px;color:#999;padding:6px 0 0 24px}
.email svg{position:absolute;left:8px;top:8px}
.btn-subscribe{position:absolute;left:648px;top:22px;width:54px;height:25px;background:var(--navy);color:var(--white);font-family:"Noto Serif",serif;font-style:italic;font-size:9.5px;display:flex;align-items:center;justify-content:center}
.site-footer{position:absolute;top:956px;left:0;width:1200px;height:84px;background:var(--navy-deep)}
.copyright{position:absolute;left:240px;top:36px;font-size:9.5px;color:var(--white)}
.footer-brand{position:absolute;left:850px;top:14px;width:104px;display:flex;flex-direction:column;align-items:center;gap:6px}
.footer-brand .brand-dot{background:var(--white);width:30px;height:30px}
.footer-brand .brand-name{color:var(--white)}
</style>
</head>
<body>
<header class="site-header">
  <div class="brand"><span class="brand-dot"></span><span class="brand-name">Velun Tresk, PLLC</span></div>
  <div class="header-divider"></div>
  <nav class="main-nav">
    <a class="active" style="left:403px">Home</a>
    <a style="left:457px">About Velun</a>
    <a style="left:536px">Practice Area</a>
    <a style="left:626px">Lawyers</a>
    <a style="left:691px">Case Study</a>
    <a style="left:769px">Contact Us</a>
  </nav>
  <div class="contact-top">
    <div><svg width="11" height="11" viewBox="0 0 24 24"><path fill="#1d2470" d="M6.6 10.8a15 15 0 0 0 6.6 6.6l2.2-2.2c.3-.3.7-.4 1-.2 1.1.4 2.3.6 3.6.6.6 0 1 .4 1 1V20c0 .6-.4 1-1 1A17 17 0 0 1 3 4c0-.6.4-1 1-1h3.5c.6 0 1 .4 1 1 0 1.3.2 2.5.6 3.6.1.3 0 .7-.2 1z"/></svg>123.456.7894</div>
    <div><svg width="9" height="12" viewBox="0 0 12 16"><path fill="#1d2470" d="M6 0a6 6 0 0 0-6 6c0 4.5 6 10 6 10s6-5.5 6-10a6 6 0 0 0-6-6zm0 8.5A2.5 2.5 0 1 1 6 3.5a2.5 2.5 0 0 1 0 5z"/></svg>Our Map</div>
  </div>
</header>

<section class="hero">
  <div class="hero-visual" role="img" aria-label="Photo of a lawyer in a dark suit against a deep blue background"></div>
  <div class="hero-copy">
    <h2 class="hero-title">We provide legal<br>help for you!</h2>
    <p class="hero-text">The point of using Lorem Ipsum is that it has a more-or-less normal distribution of letters, as opposed to using 'Content here, content here making it look like readable English.</p>
    <span class="btn-light">Read More</span>
  </div>
  <div class="arrow" style="left:61px"><svg width="10" height="13" viewBox="0 0 10 13"><path d="M7 1L2 6.5 7 12" stroke="#111" stroke-width="2.6" fill="none"/></svg></div>
  <div class="arrow" style="left:1111px"><svg width="10" height="13" viewBox="0 0 10 13"><path d="M3 1l5 5.5L3 12" stroke="#111" stroke-width="2.6" fill="none"/></svg></div>
</section>

<section class="intro">
  <h1>We offer our clients an <strong>Expert &amp; General legal</strong> advice.</h1>
  <p>Donec sed odio operae, eu vulputate felis rhoncus. Excepteur sint obcaecat cupiditat non proident culpa. Petierunt uti sibi concilium totius Galliae in diem certam indicere. Non equidem invideo, miror magis posuere velit aliquet. Hi omnes lingua, institutis, legibus inter se differunt.</p>
  <div class="intro-actions"><span class="btn btn-dark">Read More</span><span class="btn btn-navy">Join With Us</span></div>
</section>

<div class="rule" style="top:626px"></div>

<section class="columns">
  <div class="col col-why">
    <h2>Why Us?</h2>
    <p>Lorem Ipsum is that it has a more-or-less normal distribution of letters, as opposed to using 'Content here, content here', making it look like readable English.</p>
    <p style="margin-top:13px">Lorem Ipsum is that it has a more-or-less normal distribution of letters, as opposed.</p>
    <span class="btn-small">Read More</span>
  </div>
  <div class="col col-what">
    <h2>What WE Do?</h2>
    <ul class="services">
      <li>Intellectual Property</li><li>Patents</li><li>Copyrights</li><li>Trademarks</li><li>Trade secrets</li><li>Healthcare Compliance</li><li>Elder law</li><li>Wills</li><li>Trusts</li>
    </ul>
  </div>
  <div class="col col-contact">
    <h2>Contact Info</h2>
    <div class="office">London Office</div>
    <p>Address: Lorum Street . ABC 123 Lorum,NYC<br>Phone: 2345 678 12<br>Fax: 12345 678 12</p>
    <div class="office" style="margin-top:6px">Canada Office</div>
    <p>Address: Lorum Street . ABC 123 Lorum,NYC<br>Phone: 2345 678 12<br>Fax: 12345 678 12</p>
  </div>
</section>

<div class="rule" style="top:828px"></div>

<section class="subscribe-band">
  <div class="quote-mark">&ldquo;</div>
  <p class="quote-text">Mauris fermentum dictum magnased laoreet aliquam telsolor dapibus elementun cursus eleifend, elit...</p>
  <div class="dots"><span></span><span></span><span></span></div>
  <div class="band-divider"></div>
  <div class="email"><svg width="11" height="8" viewBox="0 0 11 8"><rect x=".5" y=".5" width="10" height="7" fill="none" stroke="#999"/><path d="M.5.5l5 4 5-4" fill="none" stroke="#999"/></svg>e-mail address</div>
  <span class="btn-subscribe">Subscribe</span>
</section>

<footer class="site-footer">
  <p class="copyright">&copy; 2013 Velun Tresk, PLLC. All rights reserved.</p>
  <div class="footer-brand"><span class="brand-dot"></span><span class="brand-name">Velun Tresk, PLLC</span></div>
</footer>
</body>
</html>
```